New Business Cards for Tormin Group

We need a new Business Card to compliment our new logo. We are a vibrant design, manufacture and install business providing recreation areas, public parks and Municipal spaces. We want business cards that are classy, modern and clean.

We have recently changed our logo, and are celebrating our 40th anniversary. We want business cards with a new modern design to reflect our status.

Target Market(s)

Customers

Contact Information for Business Card

We need all the details of our 3 offices as per the business card attached. Please disregard the old logo on the business card, the other three files show our new logo.

Requirements
Must have
• All info as per attached business card but with new logo.
Nice to have

```html
<!DOCTYPE html>
<html lang="en">
<head>
<meta charset="utf-8">
<title>Tormin Group – Business Card</title>
<link href="https://fonts.googleapis.com/css2?family=Lato:wght@400;700&display=swap" rel="stylesheet">
<style>
  :root {
    --backdrop: #2b2b2d;
    --card: #ffffff;
    --brand-red: #e6323b;
    --charcoal: #46464c;
    --text: #2f2f33;
    --rule: #3a3a3e;
    --wash: #fbe7e3;
  }
  html, body {
    margin: 0;
    width: 1200px;
    height: 895px;
    overflow: hidden;
    background: var(--backdrop);
    font-family: "Lato", sans-serif;
  }
  .business-card {
    position: absolute;
    left: 100px;
    top: 162px;
    width: 1000px;
    height: 571px;
    background: var(--card);
    border-radius: 34px;
    overflow: hidden;
    color: var(--text);
  }
  .brand-wash {
    position: absolute;
    left: 560px;
    top: 330px;
    width: 420px;
    height: 420px;
    border-radius: 50%;
    background: var(--wash);
    opacity: .6;
  }
  .brand {
    position: absolute;
    left: 80px;
    top: 150px;
    display: flex;
    align-items: center;
    gap: 18px;
  }
  .brand-dot {
    width: 84px;
    height: 84px;
    border-radius: 50%;
    background: var(--brand-red);
  }
  .brand-name {
    font-weight: 700;
    font-size: 46px;
    letter-spacing: 1px;
    color: var(--charcoal);
    text-transform: uppercase;
  }
  .offices {
    position: absolute;
    right: 60px;
    top: 34px;
    text-align: right;
    font-size: 17px;
    line-height: 20px;
  }
  .office { margin-bottom: 16px; }
  .label { color: var(--brand-red); }
  .office-title { color: var(--brand-red); font-size: 18px; }
  .divider {
    position: absolute;
    left: 60px;
    right: 60px;
    top: 420px;
    height: 1.5px;
    background: var(--rule);
  }
  .person {
    position: absolute;
    left: 60px;
    top: 340px;
  }
  .person-name {
    margin: 0;
    font-weight: 400;
    font-size: 38px;
    line-height: 42px;
    color: var(--brand-red);
  }
  .person-role {
    margin: 0;
    font-size: 18px;
    line-height: 24px;
  }
  .personal-contact {
    position: absolute;
    left: 60px;
    top: 432px;
    font-size: 18px;
    line-height: 26px;
  }
  .company-contact {
    position: absolute;
    right: 60px;
    top: 432px;
    text-align: right;
    font-size: 18px;
    line-height: 26px;
  }
  .base-band {
    position: absolute;
    left: 0;
    bottom: 0;
    width: 1000px;
    height: 26px;
  }
</style>
</head>
<body>
  <div class="business-card">
    <div class="brand-wash" role="img" aria-label="Faint brand circle in soft red"></div>

    <div class="brand">
      <div class="brand-dot"></div>
      <div class="brand-name">Tormin Group</div>
    </div>

    <div class="offices">
      <div class="office">
        <div class="office-title">Head Office</div>
        <div>P.O. Box: 4812 Abu Dhabi, U.A.E.</div>
        <div>Tel: +971 (0)2 5538210</div>
        <div>Fax: +971 (0)2 5538211</div>
      </div>
      <div class="office">
        <div class="office-title">Dubai Office</div>
        <div>P.O. Box: 271846 Dubai, U.A.E.</div>
        <div>Tel: +971 (0)4 3862045</div>
        <div>Fax: +971 (0)4 3862046</div>
      </div>
      <div class="office">
        <div class="office-title">Qatar Office</div>
        <div>P.O. Box: 20731 Doha, Qatar</div>
        <div>Tel: +974 44718306</div>
        <div>Fax: +974 44718307</div>
      </div>
    </div>

    <div class="person">
      <h1 class="person-name">Rami Solvane</h1>
      <p class="person-role">Managing Partner</p>
    </div>

    <div class="divider"></div>

    <div class="personal-contact">
      <div><span class="label">Phone:</span> +971 (0)50 384 7162</div>
      <div><span class="label">Email:</span> rami@tormingroup.com</div>
    </div>

    <div class="company-contact">
      <div><span class="label">Email:</span> hello@tormingroup.com</div>
      <div><span class="label">Web:</span> www.tormingroup.com</div>
    </div>

    <svg class="base-band" viewBox="0 0 1000 26" aria-hidden="true">
      <polygon points="0,0 640,0 630,26 0,26" fill="var(--charcoal)"/>
      <polygon points="655,0 1000,0 1000,26 645,26" fill="var(--brand-red)"/>
    </svg>
  </div>
</body>
</html>
```